Request for Business Card Design

Hi. My name is Marlene, I am looking for a new business card design for my company, Quarrow Signal Instruments, LLC. I really like the design you did for Tarsel Venture and was hoping you could do something similar using our full logo and our mark. I am also open to any raised texture design using our mark. I have attached our full logo, which would need to be somewhere on the card, as well as the mark in both outline and full form, as well as our brand colors / guide. The card does not have to be white, as long as our logo and mark appear. I actually like darker colored business cards more, but am open to all options. If you are interested in working with me, please let me know. We would also take the business card design into letterhead design if you can do that.

```html
<!DOCTYPE html>
<html lang="en">
<head>
<meta charset="utf-8">
<title>Quarrow Signal Instruments — Business Card</title>
<link href="https://fonts.googleapis.com/css2?family=Barlow:wght@400;600&display=swap" rel="stylesheet">
<style>
  :root {
    --backdrop: #2b2b2b;
    --card-blue: #0a9bc2;
    --card-ink: #ffffff;
    --card-shadow: rgba(0,0,0,0.45);
  }
  * { margin: 0; padding: 0; box-sizing: border-box; }
  html, body { width: 1200px; height: 875px; overflow: hidden; }
  body {
    background: var(--backdrop);
    font-family: "Barlow", sans-serif;
    color: var(--card-ink);
    position: relative;
  }
  .card {
    position: absolute;
    width: 525px;
    height: 300px;
    background: var(--card-blue);
    border-radius: 26px;
    box-shadow: 0 14px 30px var(--card-shadow);
  }
  .card--front { left: 70px; top: 110px; }
  .card--back { left: 605px; top: 465px; }

  /* brand lockup */
  .brand { display: flex; align-items: center; gap: 16px; }
  .brand__dot { width: 46px; height: 46px; border-radius: 50%; background: var(--card-ink); flex: none; }
  .brand__name { font-weight: 600; line-height: 1; text-transform: uppercase; }
  .brand__name span { display: block; }

  .card--front .brand {
    position: absolute; left: 50%; top: 50%;
    transform: translate(-50%, -50%);
  }
  .card--front .brand__name .word-main { font-size: 52px; letter-spacing: 5px; }
  .card--front .brand__name .word-sub { font-size: 15px; letter-spacing: 1.2px; margin-top: 6px; }

  .card--back .brand { position: absolute; right: 38px; top: 34px; gap: 12px; }
  .card--back .brand__dot { width: 32px; height: 32px; }
  .card--back .brand__name .word-main { font-size: 32px; letter-spacing: 3px; }
  .card--back .brand__name .word-sub { font-size: 9.5px; letter-spacing: 0.8px; margin-top: 4px; }

  .divider { position: absolute; height: 1px; background: var(--card-ink); }
  .divider--wide { left: 38px; right: 38px; top: 128px; }
  .divider--short { left: 38px; width: 150px; top: 200px; }

  .holder { position: absolute; left: 38px; top: 146px; }
  .holder__name { font-size: 24px; font-weight: 600; letter-spacing: 0.5px; text-transform: uppercase; line-height: 1.1; }
  .holder__role { font-size: 13px; letter-spacing: 0.8px; text-transform: uppercase; margin-top: 4px; }

  .contact { position: absolute; left: 38px; top: 212px; list-style: none; font-size: 14px; }
  .contact li { display: flex; align-items: center; gap: 10px; height: 22px; }
  .contact svg { width: 13px; height: 13px; flex: none; }

  .address { position: absolute; right: 38px; bottom: 40px; text-align: right; font-size: 14px; line-height: 1.35; }
</style>
</head>
<body>

  <section class="card card--front" aria-label="Business card front">
    <div class="brand">
      <div class="brand__dot"></div>
      <div class="brand__name">
        <span class="word-main">Quarrow</span>
        <span class="word-sub">Signal Instruments</span>
      </div>
    </div>
  </section>

  <section class="card card--back" aria-label="Business card back">
    <div class="brand">
      <div class="brand__dot"></div>
      <div class="brand__name">
        <span class="word-main">Quarrow</span>
        <span class="word-sub">Signal Instruments</span>
      </div>
    </div>

    <div class="divider divider--wide"></div>

    <div class="holder">
      <p class="holder__name">Dorian Pell</p>
      <p class="holder__role">Managing Director</p>
    </div>

    <div class="divider divider--short"></div>

    <ul class="contact">
      <li>
        <svg viewBox="0 0 16 16" aria-hidden="true"><path fill="#fff" d="M3.5 1.5l2.5 0 1 3.5-1.6 1.2a9 9 0 0 0 4.4 4.4L11 9l3.5 1v2.5c0 1-1 2-2 2C6.5 14.5 1.5 9.5 1.5 3.5c0-1 1-2 2-2z"/></svg>
        <span>044-210 378 915</span>
      </li>
      <li>
        <svg viewBox="0 0 16 16" aria-hidden="true"><rect x="1" y="3" width="14" height="10" fill="#fff"/><path d="M1 3l7 6 7-6" fill="none" stroke="#0a9bc2" stroke-width="1.3"/></svg>
        <span>info@quarrowsignal.com</span>
      </li>
      <li>
        <svg viewBox="0 0 16 16" aria-hidden="true"><g fill="none" stroke="#fff" stroke-width="1.3"><circle cx="8" cy="8" r="6.5"/><ellipse cx="8" cy="8" rx="3" ry="6.5"/><path d="M1.5 8h13M2.5 5h11M2.5 11h11"/></g></svg>
        <span>www.quarrowsignal.com</span>
      </li>
    </ul>

    <p class="address">218, Fennick Row Lane<br>45718, Calvoria</p>
  </section>

</body>
</html>
```